Medical Skincare services/menu/pricing Booklet 12 pages

We need produce a 12-page glossy, saddle-stitched booklet (5 1/2" tall X 81/2" wide). The booklet will be used as a services menu for a skin care salon. I have mocked up the booklet (w/ all copy) in WORD and I've provided a separate PDF of the accurate page order (see files attached). IMPORTANT: Feel free to use your creativity yet style-wise it should kinda match my wife's website colors and text style. Her clients are demanding so she wants a clean, high end, modern look (ala Apple maybe?). See her website for a frame of reference www.GlowWithMara.com
Updates

Target Market(s)

upscale female, professional women, teens with acne

Industry/Entity Type

Medical

Requirements
Must have
• the pics in the mock up are important. I've attached them here

```html
<!DOCTYPE html>
<html lang="en">
<head>
<meta charset="utf-8">
<title>Glow With Mara – Services Booklet</title>
<link href="https://fonts.googleapis.com/css2?family=Oswald:wght@400;500;600&family=Lato:wght@400;700&display=swap" rel="stylesheet">
<style>
:root{
  --bg:#e4e4e4;
  --page:#ffffff;
  --ink:#1a1a1a;
  --black:#141414;
  --blush:#fcf0ec;
  --silver:#c9c9c9;
  --grey-mid:#9a9a9a;
  --white:#ffffff;
}
*{margin:0;padding:0;box-sizing:border-box}
html,body{width:1200px;height:1200px;overflow:hidden}
body{background:var(--bg);font-family:"Lato",sans-serif;color:var(--ink);position:relative}
.page{position:absolute;width:558px;height:366px;background:var(--page);box-shadow:0 6px 10px rgba(0,0,0,.35);overflow:hidden}
.head{font-family:"Oswald",sans-serif;font-weight:400;text-transform:uppercase;line-height:1.15}
.body{font-size:6.4px;line-height:1.36;text-align:justify}
.photo{position:absolute}

/* cover */
.cover{left:33px;top:35px;background:var(--black)}
.cover .brand{position:absolute;left:0;right:0;top:162px;text-align:center;font-family:"Oswald",sans-serif;font-weight:600;font-size:44px;letter-spacing:3px;color:var(--silver);line-height:1}
.cover .services{position:absolute;left:0;right:0;top:225px;text-align:center;color:var(--white);font-size:7.6px;line-height:1.35}
.cover .foot{position:absolute;left:0;right:0;bottom:0;height:33px;background:var(--blush);text-align:center;font-size:9px;letter-spacing:3px;line-height:33px;font-weight:700}

/* about */
.about{left:626px;top:35px;background:var(--blush)}
.about .text{position:absolute;left:38px;top:24px;width:186px}
.about .head{font-size:19px;margin-bottom:8px}
.about .body{margin-bottom:14px}
.about .photo{left:279px;top:0;width:279px;height:366px;background:linear-gradient(160deg,#b9ab8f,#8b9a8c 45%,#c7c1b2)}

/* testimonials */
.testimonials{left:33px;top:424px}
.testimonials .bar{height:50px;background:linear-gradient(90deg,#707070,#e8e8e8 50%,#8a8a8a);border-bottom:2px solid var(--black);text-align:center}
.testimonials .bar .head{font-weight:600;font-size:17px;line-height:50px}
.quote{position:absolute;font-size:6.8px;line-height:1.4}
.quote p{padding-left:10px;position:relative}
.quote p::before{content:"";position:absolute;left:0;top:3px;width:3.5px;height:3.5px;border-radius:50%;background:var(--ink)}
.quote .sign{margin-top:8px}
.quote .mark{display:block;height:12px;font-family:"Oswald",sans-serif;font-weight:600;font-size:24px;color:var(--grey-mid);line-height:24px;overflow:visible}
.quote .who{font-family:"Oswald",sans-serif;font-size:11px;line-height:1.3}
.quote .who small{font-size:8px}

/* menu */
.menu{left:626px;top:424px}
.menu .photo{left:60px;top:0;width:200px;height:147px;background:linear-gradient(90deg,#f3e6dc,#e2c8b4 50%,#f6ece4)}
.menu .machine{left:410px;top:12px;width:80px;height:130px;background:linear-gradient(180deg,#3a5f9a,#c9d4e2)}
.menu .product{position:absolute;left:170px;top:80px;font-family:"Oswald",sans-serif;font-size:28px;color:#2f3440}
.menu .product span{color:#3b8fd6}
.menu .tag{position:absolute;left:296px;top:120px;font-size:7.5px}
.menu .rule{position:absolute;left:0;right:0;top:148px;height:3px;background:var(--black)}
.menu .list{position:absolute;left:30px;right:30px;top:178px;text-align:center}
.menu .item{margin-bottom:9px}
.menu .item .head{font-size:9.5px;font-weight:600}
.menu .item p{font-size:7px;line-height:1.35}
.menu .band{position:absolute;left:0;right:0;bottom:0;height:15px;background:var(--black)}

/* contact */
.contact{left:312px;top:826px;background:var(--black);color:var(--white)}
.contact .panel{position:absolute;left:0;top:0;width:332px;height:366px;background:linear-gradient(90deg,#1c1c1c,#2a2a2a)}
.contact .photo{left:332px;top:0;width:226px;height:366px;background:linear-gradient(170deg,#d8cfc8,#6d5a4c 50%,#3e3a38)}
.contact .info{position:absolute;left:14px;top:14px}
.contact .head{font-size:16px;margin-bottom:4px}
.contact .row{display:flex;gap:6px;font-size:10px;font-weight:700;line-height:1.4}
.contact .row svg{flex:none;margin-top:3px}
.contact .group{margin-bottom:10px}
.contact .brand{position:absolute;left:16px;bottom:20px;font-family:"Oswald",sans-serif;font-weight:600;font-size:24px;letter-spacing:1px;color:var(--silver)}
</style>
</head>
<body>

<section class="page cover">
  <div class="brand">GLOW WITH MARA</div>
  <div class="services">• AquaPeel Pro &nbsp;• Laser Renew &nbsp;• PL(Brightlight)<br>Vascular &nbsp;• Microneedling Pro &nbsp;• LED Light Therapy<br>Vita Peel &nbsp;• Customized Facials &amp; Peels &nbsp;• Dermaplane</div>
  <div class="foot">www.GlowWithMara.com</div>
</section>

<section class="page about">
  <div class="text">
    <h2 class="head">Mara Ellison Medical<br>Aesthetician &amp; Owner</h2>
    <p class="body">As a teenager, I had cystic acne so bad that I would ditch school to swim in the ocean because the salt water seemed to dry out and heal my skin. I was on such a mission to clear my skin that I spent my weekly allowance on skin care products I saw on TV. Then, I memorized every ingredient. I was so intrigued by the beauty industry that, by 19, I began a career as a make up artist for Lumiere, Maven, Bella Brune, Prescia, and Stelle. By 23, I was a skincare consultant for the Genevieve Kline Salons in Beverly Hills and Orange County California. I was honored to learn from the world's most demanding clients.</p>
    <h2 class="head">I understand why<br>your skin matters</h2>
    <p class="body">Admit it. We take more pictures of ourselves than ever...and then try to "fix" our blemishes with photo filters. I understand your frustrations. Some of you know I've had a parallel career as a professional singer with dozens of network TV appearances; where the HD cameras take extreme close ups...Yikes!). I also sing the National Anthem at pro football, basketball and baseball games, where their 200 foot-wide screens constantly remind me that skin imperfections are magnified. I will help get your skin more naturally beautiful so you can use less photo filters ;-)</p>
  </div>
  <div class="photo" role="img" aria-label="Portrait of the owner standing beside stone columns in a patterned maxi dress"></div>
</section>

<section class="page testimonials">
  <div class="bar"><h2 class="head">Testimonials</h2></div>
  <div class="quote" style="left:28px;top:62px;width:240px">
    <p>Mara is someone I definitely trust with my skincare needs because she truly cares about people and their issues.</p>
    <div class="sign" style="padding-left:66px"><span class="mark">“</span><div class="who">GWEN ROWLEY<br><small>Reality TV Star</small></div></div>
  </div>
  <div class="quote" style="left:300px;top:62px;width:230px">
    <p>I have been seeing Mara Ellison for AquaPeels. Ever since my first AquaPeel my skin has had a healthy glow and texture. As an Aesthetic Professional, she helps me feel my personal best.</p>
    <div class="sign" style="padding-left:124px;margin-top:10px"><span class="mark">“</span><div class="who">CARA WALSH, <small>R.N.</small></div></div>
  </div>
  <div class="quote" style="left:28px;top:172px;width:240px">
    <p>Having ethnic skin I've been hesitant about having treatments but Mara immediately put me at ease. She has taught me so much about my skin and how to care for it. Each time I've left with my skin looking and feeling amazing.</p>
    <div class="sign" style="padding-left:76px"><span class="mark">“</span><div class="who">MELODY HART - <small>Real Estate Agent</small></div></div>
  </div>
  <div class="quote" style="left:286px;top:172px;width:240px">
    <p>I have now had two facials by Mara and each time my skin feels so refreshed and new! She has also helped my teenage son who has acne. Mara knew exactly what he needed and is already getting clearer skin. Worth every penny.</p>
    <div class="sign" style="padding-left:76px"><span class="mark">“</span><div class="who">KASEY MOORE - <small>Mother of Five</small></div></div>
  </div>
  <div class="quote" style="left:32px;top:282px;width:500px">
    <p>I've been seeing Mara on a regular basis because she always goes above and beyond to ensure that I'm comfortable. She made the experience all about me and my skincare needs. She is highly knowledgable and offers creative options to make sure I get what I need.</p>
    <div class="sign" style="padding-left:340px"><span class="mark">“</span><div class="who">ELIN STAVROS - <small>Marketing Exec.</small></div></div>
  </div>
</section>

<section class="page menu">
  <div class="photo" role="img" aria-label="Close-up of a smiling woman's face with fine arrows showing lifting"></div>
  <div class="product">AquaPeel <span>Pro</span></div>
  <div class="tag">Radiance Every Day</div>
  <div class="photo machine" role="img" aria-label="Facial treatment machine with screen on a wheeled cart"></div>
  <div class="rule"></div>
  <div class="list">
    <div class="item"><h3 class="head">AquaPeel Pro is for...</h3><p>Fine Lines and Wrinkles - Elasticity and Firmness - Even Skin Tone and Vibrancy - Oil and Congested skin - Enlarged Pores - Brown Spots</p></div>
    <div class="item"><h3 class="head">Signature AquaPeel $149 (30 min)</h3><p>Deep cleanse and exfoliation, extracts, and hydrates your skin utilizing super serums filled with antioxidants, peptides and hyaluronic acid</p></div>
    <div class="item"><h3 class="head">Age-Refinement AquaPeel $175</h3><p>Includes DermaFill Serum to reduce the appearance of fine lines and wrinkles. Plumps your skin to a youthful state.</p></div>
    <div class="item"><h3 class="head">Platinum AquaPeel $250</h3><p>The ultimate AquaPeel Experience! Begin the detoxification process with Lymphatic Drainage. Then, the signature AquaPeel deeply cleanses, exfoliates, extracts and hydrates the skin while addressing your specific skin concern with a Booster of your choice. Treatment concludes with LED Light Therapy to reduce signs of aging.</p></div>
  </div>
  <div class="band"></div>
</section>

<section class="page contact">
  <div class="panel"></div>
  <div class="photo" role="img" aria-label="Portrait of the owner in a grey fur wrap with long wavy hair"></div>
  <div class="info">
    <div class="group">
      <h2 class="head">Book Online</h2>
      <div class="row"><svg width="9" height="9" viewBox="0 0 10 10"><path d="M2 1l2 2-1 1.5a6 6 0 0 0 2.5 2.5L7 6l2 2-1.5 1.5C4.5 9.5 .5 5.5.5 2.5z" fill="#fff"/></svg>(720) 555-0148</div>
      <div class="row"><svg width="9" height="9" viewBox="0 0 10 10" fill="none" stroke="#fff"><circle cx="5" cy="5" r="4.3"/><path d="M.7 5h8.6M5 .7c-2.4 2.8-2.4 5.8 0 8.6M5 .7c2.4 2.8 2.4 5.8 0 8.6"/></svg>www.GlowWithMara.com</div>
    </div>
    <div class="group">
      <h2 class="head">Location:</h2>
      <div class="row"><svg width="9" height="11" viewBox="0 0 10 12"><path d="M5 0a4 4 0 0 1 4 4c0 3-4 8-4 8S1 7 1 4a4 4 0 0 1 4-4z" fill="#fff"/><circle cx="5" cy="4" r="1.5" fill="#141414"/></svg><span>Glow With Mara<br>4210 Aspen Ridge Ave #200<br>Pine Hollow, Colorado 80199</span></div>
    </div>
    <div class="group">
      <h2 class="head">By Appt. Hours:</h2>
      <div class="row"><svg width="9" height="9" viewBox="0 0 10 10"><circle cx="5" cy="5" r="5" fill="#fff"/><path d="M5 2v3h2.5" stroke="#141414" fill="none"/></svg><span>Monday: 10:00-am-4:00pm<br>Tuesday: 10:00pm-6:00pm<br>Wednesday: 10:00am-6:00pm<br>Thursda: 10:00am-6:00pm<br>Friday: 10:00am-6:00pm<br>Saturday: 10:00-4:00pm<br>Sunday: Closed</span></div>
    </div>
  </div>
  <div class="brand">GLOW WITH MARA</div>
</section>

</body>
</html>
```